RW Framewell Inc Business cards

We need business cards using our existing logo but slightly modified. Right now the logo says RW Loadbearing Masonry. We want to keep the RW part of the design, but replace the Structural Concrete portion with "FRAMEWELL". Please see the attached file.
Ideally this would be a blank template so we can add Different Names, titles, and phone numbers later.
On the one side we want only the logo and on the other side the detail. I'm attaching an example for you to see.
Please reach out with any other questions. Our address and other details will be given out once we find a design we like.

Target Market(s)

Construction Industry

```html
<!DOCTYPE html>
<html lang="en">
<head>
<meta charset="utf-8">
<title>RW Framewell Inc – Business Cards</title>
<link href="https://fonts.googleapis.com/css2?family=Montserrat:wght@700&family=Roboto:wght@400;500;700&display=swap" rel="stylesheet">
<style>
  :root {
    --bg: #cfcfcf;
    --card: #ffffff;
    --brand-blue: #2e62a6;
    --brand-grey: #6b6b6b;
    --text-light: #ffffff;
    --shadow: rgba(0, 0, 0, 0.18);
  }
  * { margin: 0; padding: 0; box-sizing: border-box; }
  html, body {
    width: 1200px;
    height: 852px;
    overflow: hidden;
    background: var(--bg);
  }
  .stage {
    position: relative;
    width: 1200px;
    height: 852px;
    display: flex;
    align-items: center;
    justify-content: center;
    gap: 48px;
  }
  .card {
    position: relative;
    width: 520px;
    height: 297px;
    background: var(--card);
    border-radius: 22px;
    overflow: hidden;
    box-shadow: 0 6px 18px var(--shadow);
  }
  .wordmark {
    position: absolute;
    display: flex;
    flex-direction: column;
    align-items: flex-start;
    font-family: "Montserrat", sans-serif;
    font-weight: 700;
    color: var(--brand-blue);
    line-height: 1;
  }
  .wordmark__initials {
    font-size: 96px;
    letter-spacing: -2px;
  }
  .wordmark__name {
    font-size: 22px;
    letter-spacing: 6px;
    margin-top: 6px;
  }
  .card--front .wordmark {
    left: 50%;
    top: 50%;
    transform: translate(-50%, -50%);
  }
  .card--back .wordmark {
    left: 44px;
    top: 82px;
  }
  .card--back .wordmark__initials { font-size: 78px; }
  .card--back .wordmark__name { font-size: 18px; letter-spacing: 5px; }

  .back-shape {
    position: absolute;
    inset: 0;
  }
  .details {
    position: absolute;
    left: 318px;
    top: 62px;
    color: var(--text-light);
    font-family: "Roboto", sans-serif;
  }
  .details__name {
    font-size: 20px;
    font-weight: 700;
  }
  .details__title {
    font-size: 13px;
    margin-top: 4px;
    margin-left: 14px;
  }
  .contact {
    list-style: none;
    margin-top: 20px;
    margin-left: 14px;
    font-size: 12.5px;
    line-height: 1.5;
  }
  .contact__item {
    display: flex;
    align-items: flex-start;
    gap: 8px;
  }
  .contact__icon {
    flex: 0 0 12px;
    width: 12px;
    height: 12px;
    margin-top: 3px;
  }
  .contact__item--address { margin-top: 4px; }
</style>
</head>
<body>
<main class="stage">

  <section class="card card--front" aria-label="Card front">
    <div class="wordmark">
      <span class="wordmark__initials">RW</span>
      <span class="wordmark__name">FRAMEWELL</span>
    </div>
  </section>

  <section class="card card--back" aria-label="Card back">
    <svg class="back-shape" viewBox="0 0 520 297" preserveAspectRatio="none" aria-hidden="true">
      <path d="M232 0 Q 318 120 312 297 L520 297 L520 0 Z" fill="var(--brand-grey)"/>
      <path d="M244 0 Q 330 120 324 297 L520 297 L520 0 Z" fill="var(--brand-blue)"/>
    </svg>

    <div class="wordmark">
      <span class="wordmark__initials">RW</span>
      <span class="wordmark__name">FRAMEWELL</span>
    </div>

    <div class="details">
      <p class="details__name">Dan RW Carter</p>
      <p class="details__title">Managing Director</p>
      <ul class="contact">
        <li class="contact__item">
          <svg class="contact__icon" viewBox="0 0 12 12" aria-hidden="true">
            <path d="M2.5 1 L4.5 1 L5.2 3.6 L4 4.6 Q5 7 7.4 8 L8.4 6.8 L11 7.5 L11 9.5 Q10.5 11 9 11 Q1 10 1 3 Q1 1.5 2.5 1 Z" fill="var(--text-light)"/>
          </svg>
          <span>555-010-2040</span>
        </li>
        <li class="contact__item">
          <svg class="contact__icon" viewBox="0 0 12 12" aria-hidden="true">
            <rect x="1" y="2.5" width="10" height="7" rx="1" fill="var(--text-light)"/>
            <path d="M1.5 3 L6 6.5 L10.5 3" fill="none" stroke="var(--brand-blue)" stroke-width="1"/>
          </svg>
          <span>dan@framewellinc.com</span>
        </li>
        <li class="contact__item">
          <svg class="contact__icon" viewBox="0 0 12 12" aria-hidden="true">
            <circle cx="6" cy="6" r="4.8" fill="none" stroke="var(--text-light)" stroke-width="1.2"/>
            <ellipse cx="6" cy="6" rx="2" ry="4.8" fill="none" stroke="var(--text-light)" stroke-width="1"/>
            <line x1="1.2" y1="6" x2="10.8" y2="6" stroke="var(--text-light)" stroke-width="1"/>
          </svg>
          <span>www.framewellinc.com</span>
        </li>
        <li class="contact__item contact__item--address">
          <svg class="contact__icon" viewBox="0 0 12 12" aria-hidden="true">
            <path d="M6 11 Q2 6.5 2 4.5 A4 4 0 0 1 10 4.5 Q10 6.5 6 11 Z" fill="var(--text-light)"/>
            <circle cx="6" cy="4.5" r="1.4" fill="var(--brand-blue)"/>
          </svg>
          <span>410 Brickyard Rd., Millbrook,<br>Oregon, US 970012</span>
        </li>
      </ul>
    </div>
  </section>

</main>
</body>
</html>
```